UI/ UX Design for ERP Software

We need a new UX/UI interface for a ERP software for property managers. Our CMMS / ERP solution is made based on responsive design technologies and is coded in PHP.
The overall UX to be similar to Tev Ulna - easy navigation, intuitive menus.

Industry/Entity Type

Property Management

Number of Pages Required

5+ page

Requirements
Must have
• Round dock buttons
Consistent icons across the application
Enough Spacing between buttons/icons/ menu
Consistent Font
Nice to have
• We would like the UX to allow the users to use the application without /minimum training.
Should not have
• we don't want anything that is classic with respect to UX

```html
<!DOCTYPE html>
<html lang="en">
<head>
<meta charset="utf-8">
<title>Estavia – Active Dashboard</title>
<link rel="stylesheet" href="https://fonts.googleapis.com/css2?family=IBM+Plex+Sans:wght@400;500;600;700&display=swap">
<style>
  :root {
    --page-bg: #f7f7f7;
    --surface: #ffffff;
    --ink: #1c1c1c;
    --muted: #6b6b6b;
    --accent: #0db4f3;
    --brand: #1f8fe6;
    --slate: #556479;
    --line: #e6e6e6;
    --card-border: #d9d9d9;
    --icon: #4a5668;
    --dot-green: #8ee07a;
    --dot-blue: #0db4f3;
    --dot-orange: #f2a25a;
    --dot-dark: #404040;
    --dot-violet: #8088e6;
    --dot-pink: #f25577;
    --dot-purple: #c75af2;
  }
  * { box-sizing: border-box; margin: 0; padding: 0; }
  html, body { width: 1200px; height: 858px; overflow: hidden; }
  body {
    background: var(--page-bg);
    font-family: "IBM Plex Sans", Arial, sans-serif;
    color: var(--ink);
    position: relative;
  }
  .app-header {
    position: absolute; left: 0; top: 0; width: 1200px; height: 111px;
    background: var(--surface);
    box-shadow: 0 1px 3px rgba(0,0,0,.05);
  }
  .brand {
    position: absolute; left: 133px; top: 28px;
    display: flex; align-items: center; gap: 8px;
    font-size: 30px; font-weight: 600; color: var(--brand); letter-spacing: -0.5px;
  }
  .brand-mark { width: 26px; height: 26px; background: var(--brand); border-radius: 50%; }
  .nav-link {
    position: absolute; font-size: 9.6px; color: var(--ink);
    text-transform: uppercase; white-space: nowrap; line-height: 1;
  }
  .utility-nav .nav-link { top: 39px; }
  .main-nav .nav-link { top: 85px; }
  .caret {
    display: inline-block; margin-left: 6px; vertical-align: middle;
    border-left: 3.5px solid transparent; border-right: 3.5px solid transparent;
    border-top: 4px solid var(--ink);
  }
  .page-title {
    position: absolute; left: 132px; top: 152px;
    font-size: 14.5px; font-weight: 700; letter-spacing: .3px;
  }
  .range-picker {
    position: absolute; left: 873px; top: 144px; width: 172px; height: 32px;
    background: var(--slate); color: #fff; border-radius: 2px;
    font-size: 10.5px; font-weight: 600; letter-spacing: .4px;
    display: flex; align-items: center; justify-content: space-between; padding: 0 10px 0 13px;
  }
  .stat-card {
    position: absolute; top: 204px; width: 175px; height: 100px;
    background: var(--surface); border: 1px solid var(--card-border);
    text-align: center;
  }
  .stat-icon { position: absolute; left: 50%; top: 13px; margin-left: -14px; width: 28px; height: 28px; }
  .stat-value {
    position: absolute; left: 0; right: 0; top: 48px;
    font-size: 14px; font-weight: 600; color: var(--accent);
  }
  .stat-label {
    position: absolute; left: 0; right: 0; top: 68px;
    font-size: 10px; text-transform: uppercase; color: var(--ink);
  }
  .chart-panel {
    position: absolute; left: 133px; top: 339px; width: 913px; height: 426px;
    background: var(--surface); box-shadow: 0 0 4px rgba(0,0,0,.06);
  }
  .chart-panel svg { display: block; }
  .axis-text { font-family: "IBM Plex Sans", Arial, sans-serif; font-size: 7.5px; fill: var(--muted); }
  .legend-text { font-family: "IBM Plex Sans", Arial, sans-serif; font-size: 9px; fill: #333; }
  .app-footer {
    position: absolute; left: 0; width: 1200px; top: 807px;
    text-align: center; font-size: 10px; color: var(--ink);
  }
</style>
</head>
<body>
  <header class="app-header">
    <div class="brand"><span class="brand-mark"></span>Estavia</div>
    <nav class="utility-nav">
      <span class="nav-link" style="left:777px">Files</span>
      <span class="nav-link" style="left:822px">Pages</span>
      <span class="nav-link" style="left:880px">Configurations</span>
      <span class="nav-link" style="left:989px">Settings</span>
    </nav>
    <nav class="main-nav">
      <span class="nav-link" style="left:135px">Dashboard</span>
      <span class="nav-link" style="left:205px">Customers</span>
      <span class="nav-link" style="left:276px">Properties</span>
      <span class="nav-link" style="left:351px">Tenants</span>
      <span class="nav-link" style="left:410px">Contacts</span>
      <span class="nav-link" style="left:477px">Contractors</span>
      <span class="nav-link" style="left:559px">Employees</span>
      <span class="nav-link" style="left:633px">Compliance Managemem</span>
      <span class="nav-link" style="left:782px">Prevent. Maintenance</span>
      <span class="nav-link" style="left:917px">Work Orders</span>
      <span class="nav-link" style="left:1000px">More<span class="caret"></span></span>
    </nav>
  </header>

  <main>
    <h1 class="page-title">ACTIVE DASHBOARD</h1>
    <div class="range-picker">
      <span>LAST 7 DAYS</span>
      <svg width="11" height="11" viewBox="0 0 12 12" fill="none" stroke="#fff" stroke-width="1.2">
        <rect x="1" y="2.5" width="10" height="8.5" rx="1"/><path d="M1 5h10M3.5 1v3M8.5 1v3"/>
      </svg>
    </div>

    <section class="stat-card" style="left:133px">
      <svg class="stat-icon" viewBox="0 0 28 28" fill="var(--icon)">
        <rect x="3" y="6" width="12" height="19"/><rect x="15" y="11" width="10" height="14"/>
        <g fill="#fff"><rect x="5" y="9" width="2.5" height="2.5"/><rect x="10" y="9" width="2.5" height="2.5"/><rect x="5" y="14" width="2.5" height="2.5"/><rect x="10" y="14" width="2.5" height="2.5"/><rect x="5" y="19" width="2.5" height="2.5"/><rect x="10" y="19" width="2.5" height="2.5"/><rect x="17" y="14" width="2.5" height="2.5"/><rect x="21" y="14" width="2.5" height="2.5"/><rect x="17" y="19" width="2.5" height="2.5"/><rect x="21" y="19" width="2.5" height="2.5"/></g>
      </svg>
      <div class="stat-value">3</div>
      <div class="stat-label">Properties</div>
    </section>
    <section class="stat-card" style="left:318px">
      <svg class="stat-icon" viewBox="0 0 28 28" fill="var(--icon)">
        <path d="M14 2 L26 8 H2 Z"/><rect x="3" y="9" width="22" height="2"/>
        <rect x="5" y="12" width="2.5" height="10"/><rect x="10" y="12" width="2.5" height="10"/><rect x="15.5" y="12" width="2.5" height="10"/><rect x="20.5" y="12" width="2.5" height="10"/>
        <rect x="3" y="23" width="22" height="2.5"/>
      </svg>
      <div class="stat-value">8</div>
      <div class="stat-label">Tenants</div>
    </section>
    <section class="stat-card" style="left:501px">
      <svg class="stat-icon" viewBox="0 0 28 28" fill="none" stroke="var(--icon)" stroke-width="1.4">
        <path d="M4 3v21h21"/><rect x="6" y="8" width="16" height="14"/>
        <path d="M6 14l8-6M6 20l14-12M10 22l12-9M16 22l6-4"/>
      </svg>
      <div class="stat-value">422,00.00 SQFT</div>
      <div class="stat-label">Total Properities Area</div>
    </section>
    <section class="stat-card" style="left:686px">
      <svg class="stat-icon" viewBox="0 0 28 28" fill="none" stroke="var(--icon)" stroke-width="1.4">
        <rect x="5" y="3" width="18" height="22" rx="1"/><path d="M9 8h6M9 12h10M9 16h10M9 20h10"/><path d="M17 6l2 2 2-2" />
      </svg>
      <div class="stat-value">233,500.00 SQFT</div>
      <div class="stat-label">Rented Area</div>
    </section>
    <section class="stat-card" style="left:871px">
      <svg class="stat-icon" viewBox="0 0 28 28" fill="none" stroke="var(--icon)" stroke-width="2">
        <circle cx="12" cy="11" r="8"/><path d="M18 17l7 7"/>
      </svg>
      <div class="stat-value">188,500 SQFT</div>
      <div class="stat-label">Vacancies Area</div>
    </section>

    <section class="chart-panel" aria-label="Maintenance and inspection activity, last 7 days">
      <svg width="913" height="426" viewBox="133 339 913 426">
        <g stroke="var(--line)" stroke-width="0.7">
          <line x1="172" y1="385" x2="1007" y2="385"/>
          <line x1="172" y1="436" x2="1007" y2="436"/>
          <line x1="172" y1="486" x2="1007" y2="486"/>
          <line x1="172" y1="538" x2="1007" y2="538"/>
          <line x1="172" y1="595" x2="1007" y2="595"/>
        </g>
        <line x1="172" y1="658" x2="1007" y2="658" stroke="#dcdcdc" stroke-width="1.5"/>
        <g class="axis-text" text-anchor="end">
          <text x="166" y="388">1.25</text><text x="166" y="439">1</text>
          <text x="166" y="489">0.75</text><text x="166" y="541">0.5</text>
          <text x="166" y="598">0.25</text><text x="166" y="661">0</text>
        </g>
        <rect x="462" y="436" width="5.5" height="222" fill="var(--accent)"/>
        <g class="axis-text" text-anchor="middle">
          <text x="224" y="685">12/27/2020</text><text x="345" y="685">12/28/2020</text>
          <text x="466" y="685">12/29/2020</text><text x="587" y="685">12/30/2020</text>
          <text x="709" y="685">12/31/2020</text><text x="830" y="685">01/01/2021</text>
          <text x="951" y="685">01/02/2021</text>
        </g>
        <g>
          <circle cx="191" cy="731" r="3.6" fill="var(--dot-green)"/>
          <circle cx="329" cy="731" r="3.6" fill="var(--dot-blue)"/>
          <circle cx="473" cy="731" r="3.6" fill="var(--dot-orange)"/>
          <circle cx="597" cy="731" r="3.6" fill="var(--dot-dark)"/>
          <circle cx="714" cy="731" r="3.6" fill="var(--dot-violet)"/>
          <circle cx="838" cy="731" r="3.6" fill="var(--dot-pink)"/>
          <circle cx="974" cy="731" r="3.6" fill="var(--dot-purple)"/>
        </g>
        <g class="legend-text" text-anchor="middle">
          <text x="191" y="753">Schedule Maintenance</text>
          <text x="329" y="753">Completed Schedule Maintenance</text>
          <text x="474" y="753">uture Schedule Maintenance</text>
          <text x="600" y="753">cheduled work orders</text>
          <text x="713" y="753">Completed work orders</text>
          <text x="838" y="753">Property Inspection in Progress</text>
          <text x="974" y="753">Complete property Inspections</text>
        </g>
      </svg>
    </section>
  </main>

  <footer class="app-footer">Copyright © 2021 All Rights Reserved</footer>
</body>
</html>
```